Vale Linebacker Needs a new website!

We need a four page website for a new company based in San Francisco. We help companies connect better with their clients, employees, and vendors by implementing collaborative technology.
Similar Websites
Mist Rangers - http://www.mistrangers.example/
Skyforthing - http://www.skyforthing.example/ - I don't like the the rotating window or the pictures of people. I like the icons used to go to the next pages.
Color Combos
Blues and Yellows - http://www.huepairings.example/palette-sets/96/HuePairing96.html
We prefer graphics over the actual pictures of people in the header. Pictures of people working together in the text is fine.
Web Page Layout
Index
Cloud Advisory Services
Email Everywhere
CRM Implementation
For detailed copy please see this link https://files.paperhold.example/a/widgetladyla.example/document/d/7KtmPzWqAeRbYcNvHsJgLdFxTuQoIeMnBvCxZaSdFgHj/edit
Industry/Entity Type
It Company

```html
<!DOCTYPE html>
<html lang="en">
<head>
<meta charset="utf-8">
<title>Vale Linebacker</title>
<link rel="stylesheet" href="https://fonts.googleapis.com/css2?family=Quicksand:wght@300;400;500;600&family=Open+Sans:ital,wght@0,400;0,600;1,400&display=swap">
<style>
:root{
  --brand-blue:#1f5bb5;
  --band-blue:#2a62b4;
  --icon-circle:#1d4f9c;
  --text-dark:#222;
  --text-heading:#333;
  --text-body:#777;
  --link-blue:#2d6cc0;
  --gold:#d9a520;
  --quote-yellow:#f2c200;
  --dark-band:#2a2a2a;
  --footer-bg:#f4f4f4;
  --legal-bg:#ebebeb;
  --white:#fff;
}
*{margin:0;padding:0;box-sizing:border-box}
html,body{width:1200px;height:3000px;overflow:hidden}
body{position:relative;background:var(--white);font-family:"Open Sans",Arial,sans-serif;color:var(--text-body)}
.section{position:absolute;left:0;width:1200px}
h1,h2,h3{font-weight:400}

/* header */
.site-header{top:0;height:116px;background:var(--white)}
.brand{position:absolute;left:132px;top:36px;display:flex;align-items:center;gap:10px}
.brand-mark{width:30px;height:30px;background:var(--brand-blue)}
.brand-name{font-family:"Open Sans",sans-serif;font-weight:600;font-size:22px;color:var(--text-heading);line-height:1}
.brand-tag{position:absolute;left:172px;top:72px;font-size:10px;color:#8a94a6;letter-spacing:.5px}
.main-nav{position:absolute;top:54px;left:458px;display:flex;gap:28px;font-family:"Quicksand",sans-serif;font-size:16px;font-weight:500;color:#333}
.main-nav .is-current{color:var(--brand-blue)}

/* hero */
.hero{top:116px;height:536px}
.hero-visual{position:absolute;inset:0;background:radial-gradient(ellipse at 30% 45%,#cfe6f6 0%,#6fb0dc 22%,#1f74b8 50%,#0d4f8f 100%)}
.hero-title{position:absolute;top:194px;width:100%;text-align:center;font-family:"Quicksand",sans-serif;font-size:50px;color:var(--white)}
.hero-sub{position:absolute;top:256px;width:100%;text-align:center;font-family:"Quicksand",sans-serif;font-size:28px;font-weight:500;color:var(--white)}
.hero-arrow{position:absolute;top:222px;width:48px;height:48px;border-radius:50%;border:4px solid rgba(120,180,225,.7)}
.hero-arrow.prev{left:0}.hero-arrow.next{right:0}
.dots{position:absolute;left:0;width:100%;display:flex;justify-content:center;gap:4px}
.dots span{width:14px;height:14px;border-radius:50%;background:var(--white)}
.hero .dots{top:510px}

/* about */
.about{top:652px;height:303px;text-align:center}
.section-title{font-family:"Quicksand",sans-serif;color:var(--text-dark);font-size:42px;font-weight:400}
.about .section-title{margin-top:52px}
.about p{width:920px;margin:18px auto 0;font-size:12px;line-height:23px}
.about p + p{margin-top:4px}

/* services */
.services{top:955px;height:495px;background:var(--band-blue);color:var(--white);text-align:center}
.services .section-title{color:var(--white);font-size:34px;font-weight:500;margin-top:50px}
.services .lead{font-size:13px;margin-top:6px}
.service{position:absolute;top:160px;width:220px;margin-left:-110px}
.service-icon{width:132px;height:132px;border-radius:50%;background:var(--icon-circle);margin:0 auto;display:flex;align-items:center;justify-content:center}
.service h3{font-family:"Quicksand",sans-serif;font-weight:600;font-size:22px;margin-top:16px}
.service p{font-size:12px;line-height:20px;margin-top:6px}

/* blog */
.blog{top:1450px;height:475px;text-align:center}
.blog .section-title{margin-top:40px;font-size:40px}
.post{position:absolute;top:114px;width:298px;height:304px;border:1px solid #dcdcdc;border-radius:3px;overflow:hidden;background:var(--white)}
.post-image{height:156px}
.post h3{font-family:"Open Sans",sans-serif;font-size:17px;color:var(--link-blue);margin-top:18px}
.post p{font-size:12px;line-height:20px;margin:8px 22px 0}

/* testimonial */
.testimonial{top:1925px;height:437px;background:var(--dark-band);text-align:center;color:var(--white)}
.testimonial-photo{position:absolute;inset:0;background:linear-gradient(90deg,#3a3028 0%,#2a2a2a 40%,#333 70%,#2a2a2a 100%)}
.testimonial .section-title{position:relative;color:var(--quote-yellow);font-family:"Open Sans",sans-serif;font-size:34px;margin-top:70px}
.quote{position:relative;width:680px;margin:14px auto 0;font-style:italic;font-size:14px;line-height:28px}
.quote-mark{font-family:Georgia,serif;font-style:normal;font-weight:700;font-size:40px;line-height:0;vertical-align:-12px}
.author{position:absolute;left:506px;top:266px;display:flex;align-items:center;gap:12px;text-align:left}
.author-photo{width:58px;height:58px;border-radius:50%;background:linear-gradient(#e8d8c8,#b8a090);border:2px solid var(--white)}
.author-name{font-size:19px;font-weight:600}
.author-place{font-size:11px}
.testimonial .dots{top:394px}

/* clients */
.clients{top:2362px;height:324px;text-align:center}
.clients .section-title{color:var(--gold);font-family:"Open Sans",sans-serif;font-size:34px;margin-top:50px}
.client{position:absolute;display:flex;align-items:center;gap:8px;transform:translate(-50%,-50%);font-size:15px;font-weight:600;color:#333;white-space:nowrap}
.client i{display:block;width:14px;height:14px;border-radius:50%;background:#2f6fb6}

/* footer */
.site-footer{top:2686px;height:250px;background:var(--footer-bg)}
.footer-col{position:absolute;top:42px}
.footer-col h4{font-family:"Open Sans",sans-serif;font-weight:400;font-size:17px;color:#333;margin-bottom:8px}
.footer-col li{list-style:none;font-size:12px;line-height:26px;color:#777}
.social{display:flex;gap:4px;margin-top:8px}
.social span{width:30px;height:30px;border-radius:50%;background:#111}
.legal{top:2936px;height:64px;background:var(--legal-bg);font-size:12px;color:#888;padding:24px 0 0 134px}
</style>
</head>
<body>

<header class="section site-header">
  <div class="brand"><span class="brand-mark"></span><span class="brand-name">Vale Linebacker</span></div>
  <div class="brand-tag">Connect. Collaborate. Grow.</div>
  <nav class="main-nav">
    <span class="is-current">Home</span>
    <span>Cloud Advisory Services</span>
    <span>Email Everywhere</span>
    <span>CRM Implementation</span>
  </nav>
</header>

<section class="section hero">
  <div class="hero-visual" role="img" aria-label="Hero graphic: a hand touching a glowing cloud symbol on a blue background"></div>
  <span class="hero-arrow prev"></span><span class="hero-arrow next"></span>
  <h1 class="hero-title">Cloud Advisory Services</h1>
  <p class="hero-sub">Pellentesque faucibus Ut accumsan ultricies Maecenas</p>
  <div class="dots"><span></span><span></span><span></span><span></span></div>
</section>

<section class="section about">
  <h2 class="section-title">About Our Company</h2>
  <p>Aliquam nec erat at purus cursus interdum Vestibulum ligula augue bibendum accumsan vestibulum ut commodo a mi Morbi ornare gravida elit Integer congue augue et malesuada iaculis ipsum dui aliquet felis at cursus magna nisl nec elit Vestibulum gravida Praesent elementum elit at tellus Malesuada nec ultricies sit amet porttitor mattis enim In massa libero interdum nec interdum vel blandit sed nulla In ullamcorper est eget tempor cu</p>
  <p>Maecenas at justo id velit placerat molestie Donec dictum lectus non odio Cras a ante vitae enim iaculis aliquam Mauris nunc quam venenatis nec euismod sit amet egestas placerat est Pellentesque habitant morbi tristique senectus et netus et malesuada fames ac turpis egestas Cras id</p>
</section>

<section class="section services">
  <h2 class="section-title">What We Do</h2>
  <p class="lead">Suspendisse quam leo molestie sed luctus quis feugiat in pede Fusce tellus Sed metus augue convallis et vehicula ut pulvinar eu</p>

  <div class="service" style="left:246px">
    <div class="service-icon">
      <svg width="64" height="64" viewBox="0 0 64 64" fill="none" stroke="#fff" stroke-width="3"><circle cx="30" cy="34" r="24"/><circle cx="30" cy="34" r="15"/><circle cx="30" cy="34" r="6"/><path d="M30 34 L56 8 M48 8 H56 V16"/></svg>
    </div>
    <h3>Strategy</h3>
    <p>Etiam eu urna Sed porta Suspendisse quam leo molestie sed luctus quis feugiat in pede Fusce</p>
  </div>

  <div class="service" style="left:488px">
    <div class="service-icon">
      <svg width="64" height="64" viewBox="0 0 64 64" fill="none" stroke="#fff" stroke-width="3"><path d="M8 6 V56 H60"/><path d="M12 44 L24 26 L34 40 L44 20 L56 32"/><path d="M12 30 L24 44 L36 22 L46 36 L56 14" stroke-width="2"/></svg>
    </div>
    <h3>Migration</h3>
    <p>Etiam eu urna Sed porta Suspendisse quam leo molestie sed luctus quis feugiat in pede Fusce</p>
  </div>

  <div class="service" style="left:738px">
    <div class="service-icon">
      <svg width="72" height="64" viewBox="0 0 72 64" fill="#fff"><path d="M18 44 a12 12 0 0 1 2-24 a16 16 0 0 1 30-4 a12 12 0 0 1 6 28 Z"/><circle cx="34" cy="50" r="8" fill="#fff" stroke="#1d4f9c" stroke-width="3"/><circle cx="50" cy="52" r="6" fill="#fff" stroke="#1d4f9c" stroke-width="3"/></svg>
    </div>
    <h3>Implementation</h3>
    <p>Etiam eu urna Sed porta Suspendisse quam leo molestie sed luctus quis feugiat in pede Fusce</p>
  </div>

  <div class="service" style="left:980px">
    <div class="service-icon">
      <svg width="64" height="64" viewBox="0 0 64 64" fill="none" stroke="#fff" stroke-width="2.5"><circle cx="32" cy="32" r="26"/><ellipse cx="32" cy="32" rx="12" ry="26"/><path d="M6 32 H58 M10 18 H54 M10 46 H54 M32 6 V58"/></svg>
    </div>
    <h3>Integration</h3>
    <p>Etiam eu urna Sed porta Suspendisse quam leo molestie sed luctus quis feugiat in pede Fusce</p>
  </div>
</section>

<section class="section blog">
  <h2 class="section-title">Recent Blog Post</h2>
  <article class="post" style="left:132px">
    <div class="post-image" role="img" aria-label="Photo: businessman touching cloud and device icons" style="background:linear-gradient(135deg,#5c6b7c,#9aa8b6 55%,#3b4654)"></div>
    <h3>Aliquam nec erat at purus</h3>
    <p>interdum Vestibulum ligula augue bibendum accumsan vestibulum ut commodo a mi Morbi ornare gravida elit Integer</p>
  </article>
  <article class="post" style="left:444px">
    <div class="post-image" role="img" aria-label="Photo: businesswoman in front of a blue cloud technology screen" style="background:linear-gradient(135deg,#2d4e86,#6f8fc2 55%,#1f3564)"></div>
    <h3>Mauris nunc quam venenatis</h3>
    <p>interdum Vestibulum ligula augue bibendum accumsan vestibulum ut commodo a mi Morbi ornare gravida elit Integer</p>
  </article>
  <article class="post" style="left:760px">
    <div class="post-image" role="img" aria-label="Illustration: glowing cloud network connected to devices" style="background:radial-gradient(circle at 50% 40%,#3fb4e0,#0b4f82 60%,#06263f)"></div>
    <h3>Duis quam Nam eget</h3>
    <p>interdum Vestibulum ligula augue bibendum accumsan vestibulum ut commodo a mi Morbi ornare gravida elit Integer</p>
  </article>
</section>

<section class="section testimonial">
  <div class="testimonial-photo" role="img" aria-label="Dimmed background photo of people working in an office"></div>
  <h2 class="section-title">What Our Customer Says</h2>
  <p class="quote"><span class="quote-mark">&ldquo;</span> Aliquam nec erat at purus cursus interdum Vestibulum ligula augue bibendum accumsan vestibulum ut commodo a mi Morbi ornare gravida elit Integer congue augue et malesuada iaculis ipsum dui aliquet felis at cursus magna nisl nec elit Vestibulum gravida Praesent elementum elit at tellus Malesuada nec ultricies sit amet porttitor mattis enim <span class="quote-mark">&rdquo;</span></p>
  <div class="author">
    <div class="author-photo" role="img" aria-label="Customer portrait"></div>
    <div><div class="author-name">By Author Name</div><div class="author-place">City, Location</div></div>
  </div>
  <div class="dots"><span></span><span></span><span></span></div>
</section>

<section class="section clients">
  <h2 class="section-title">Clients &amp; Partners</h2>
  <div class="client" style="left:258px;top:162px">Northvane</div>
  <div class="client" style="left:418px;top:162px"><i></i>Stagehall</div>
  <div class="client" style="left:612px;top:162px">Tidecrest</div>
  <div class="client" style="left:768px;top:162px">Corvel Group</div>
  <div class="client" style="left:930px;top:162px"><i></i>Amberline</div>
  <div class="client" style="left:270px;top:236px">Pellway</div>
  <div class="client" style="left:424px;top:236px">Lumora</div>
  <div class="client" style="left:604px;top:236px">Fenwick Networks</div>
  <div class="client" style="left:770px;top:236px">Quillbox</div>
  <div class="client" style="left:930px;top:236px"><i></i>Orbitnode</div>
</section>

<footer class="section site-footer">
  <div class="footer-col" style="left:132px"><h4>Company</h4><ul><li>Verra sit amet</li><li>Quam Curabitur</li><li>Ipsum dictum tristique</li><li>Praesent vitae</li></ul></div>
  <div class="footer-col" style="left:322px"><h4>Features</h4><ul><li>Accumsan vestibulum</li><li>Commodo Morbi</li><li>Ornare gravida elit</li><li>Integer congue</li></ul></div>
  <div class="footer-col" style="left:530px"><h4>Services</h4><ul><li>Verra sit amet</li><li>Quam Curabitur</li><li>Vel dolor ultrices</li><li>Ipsum dictum tristi</li></ul></div>
  <div class="footer-col" style="left:694px"><h4>Resources</h4><ul><li>Aliquam nec erat</li><li>Purus cursus interdum</li><li>Vestibulum ligula</li><li>Augue bibendum</li></ul></div>
  <div class="footer-col" style="left:908px"><h4>Get in touch</h4><div class="social"><span></span><span></span><span></span><span></span></div></div>
</footer>

<div class="section legal">&copy; 2014 Company Name.&nbsp; All right reserved.&nbsp; Term of Use</div>

</body>
</html>
```